Landing Page and Logo for Auto-Blogging Platform

I created a platform that allows users to start a blog for their business, hobby, charity, etc. I need a landing page where users can learn about the platform, benefits of consistent blogging, SEO value, plans/pricing, etc. The landing page needs to have multiple call to action buttons encouraging the visitor to register/sign up for a free trial.

In addition to the landing page, I need a page for users to establish the settings for their blog. This page should be a fairly simple form, intended for the user to enter a few details to set up their blog:
1. Name of Blog
2. Up to 10 topics and/or keywords the blog should focus on
3. Theme: Color-scheme and logo upload for blog.

I have attached the specifications of the platform's functionality so you can better understand how it works, plans/pricing, etc.

I also need a logo for the business. The name of the platform is PostNook.

Target Market(s)

Website owners, bloggers, business owners

Industry/Entity Type

Technology, Internet, web design

Coding

Coded - Design and coding required

Number of Pages Required

2 page

Colors
0054AA
0677BA
7BADD7
CADEEF
E8F1F8
0094D4
00A9DD
6FCCEA
C7EBF8
E9F6FB

Requirements
Must have
• Eye-catching design but fairly light on content (keep it simple and brief.)
Nice to have
• Eye-catching yet simple design, clean and easy to understand what we are offering.
Should not have
• Too much “wordy” and confusing content.

```html
<!DOCTYPE html>
<html lang="en">
<head>
<meta charset="utf-8">
<title>PostNook – Automate Your Blog</title>
<link rel="stylesheet" href="https://fonts.googleapis.com/css2?family=Poppins:wght@400;500;600&display=swap">
<style>
:root{
  --blue:#0054aa;
  --blue-mid:#0677ba;
  --blue-light:#00a9dd;
  --sky:#0094d4;
  --pale:#e9f6fb;
  --pale-2:#e8f1f8;
  --tint:#cadeef;
  --ink:#1c1c1c;
  --white:#fff;
  --foot:#f4f4f4;
}
*{margin:0;padding:0;box-sizing:border-box}
html,body{width:1200px;height:3526px;overflow:hidden}
body{font-family:"Poppins",sans-serif;color:var(--ink);background:var(--white);position:relative}
.abs{position:absolute}
.btn{position:absolute;display:flex;align-items:center;justify-content:center;border-radius:30px;font-weight:500;letter-spacing:.3px}
.btn-blue{background:linear-gradient(180deg,var(--blue-mid),var(--blue));color:var(--white)}
.btn-white{background:var(--white);color:var(--blue)}
.bar{position:absolute;height:5px;width:78px;background:var(--blue);border-radius:2px}
.title{position:absolute;font-size:34px;font-weight:500;color:var(--blue);letter-spacing:.5px;white-space:nowrap}
.title span{color:var(--sky)}
.copy{position:absolute;font-size:16px;line-height:38.5px;white-space:nowrap}
.logo{position:absolute;display:flex;align-items:center;gap:10px;font-size:25px;font-weight:500;color:var(--sky);letter-spacing:.5px}
.logo i{width:28px;height:28px;border-radius:50%;background:var(--sky);display:block}

.topbar{top:0;left:0;width:1200px;height:53px;background:linear-gradient(180deg,var(--blue-mid),var(--blue));display:flex;align-items:center;justify-content:center;gap:18px;color:var(--white);font-size:14px;font-weight:500}
.topbar .sign{position:static;width:103px;height:32px;font-size:13px}
.nav{top:53px;left:0;width:1200px;height:82px}
.nav a{position:absolute;top:34px;font-size:14.5px;font-weight:500;color:var(--ink);text-decoration:none}
.nav a.on{color:var(--blue)}
.nav a.on::before{content:"";position:absolute;top:-13px;left:0;width:100%;height:3px;background:var(--blue)}
.hero{top:135px;left:0;width:1200px;height:471px}
.hero-photo{left:390px;top:0;width:810px;height:471px;background:linear-gradient(135deg,#c9d3da,#a88565 55%,#6c5443)}
.hero-kicker{left:43px;top:76px;font-size:22px;color:var(--blue-light)}
.hero-h{left:42px;top:110px;font-size:46px;font-weight:500;color:var(--white);letter-spacing:.5px}
.hero-p{left:43px;top:186px;color:var(--white);font-size:16px;line-height:38.5px;white-space:nowrap}
.price-bg{left:560px;top:700px;width:640px;height:497px;background:var(--pale);border-radius:90px 0 0 90px}
.card{position:absolute;top:735px;width:287px;height:428px;background:var(--white);border:1.5px solid var(--tint);border-radius:30px;text-align:center}
.card svg{margin-top:44px}
.card h3{font-size:24px;font-weight:500;margin-top:22px}
.card hr{border:0;border-top:1px solid #c9c9c9;margin:16px 12px 0}
.card p{font-size:16px;line-height:38.5px;margin-top:14px}
.card .btn{left:55px;bottom:50px;width:177px;height:50px;font-size:18px}
.about{top:1275px;left:0;width:1200px;height:488px;background:var(--blue)}
.about-shape{left:0;top:0;width:540px;height:488px;background:var(--blue-mid);border-radius:0 120px 0 0;opacity:.35}
.dash{left:110px;top:87px;width:490px;height:313px;border-radius:14px;background:linear-gradient(135deg,#e9f6fb,#c7ebf8 60%,#7badd7)}
.step{position:absolute;top:1982px;width:230px;height:268px;background:var(--white);border-radius:18px;border-right:3px solid var(--blue);border-bottom:3px solid var(--blue);box-shadow:0 4px 16px rgba(0,84,170,.15);display:flex;flex-direction:column;align-items:center;justify-content:center;text-align:center;font-size:12.5px;line-height:32px;padding:0 10px;letter-spacing:.2px;white-space:nowrap}
.step.active{background:linear-gradient(160deg,var(--sky),var(--blue));color:var(--white);border-color:var(--tint)}
.step svg{margin-bottom:14px}
.ben-photo{left:575px;top:2342px;width:625px;height:496px;background:linear-gradient(120deg,#d9c7ae,#8a6e5a 50%,#7c4a5a);clip-path:polygon(10% 0,100% 0,100% 100%,22% 100%,0 38%,3% 12%)}
.ben-list{left:108px;top:2595px;list-style:none}
.ben-list li{display:flex;align-items:center;gap:18px;height:46px;font-size:16px;font-weight:500}
.footer{top:2935px;left:0;width:1200px;height:591px;background:var(--foot)}
.foot-panel{left:0;top:43px;width:540px;height:427px}
.foot-h{position:absolute;font-size:22px;font-weight:500}
.contact li{display:flex;align-items:center;gap:16px;height:60px;font-size:15px;font-weight:500;color:#333}
.links{position:absolute;list-style:none}
.links li{height:46px;font-size:15px;color:#333;letter-spacing:.3px}
.rule{left:93px;top:518px;width:1014px;border-top:1px solid #b9b9b9}
.copyright{left:93px;top:547px;font-size:15px;color:#333}
.pays{left:714px;top:535px;display:flex;gap:12px}
.pays span{width:70px;height:40px;background:var(--white);border:1px solid #ccc;border-radius:5px;display:flex;align-items:center;justify-content:center;font-size:13px;font-weight:600;color:var(--blue)}
</style>
</head>
<body>

<header class="abs topbar">
  <span>WANT YOUR SITE TO PAY ?</span>
  <span class="btn btn-white sign">SIGN UP</span>
</header>

<nav class="abs nav">
  <div class="logo" style="left:117px;top:26px"><i></i>POSTNOOK</div>
  <a class="on" style="left:488px">HOME</a>
  <a style="left:578px">HOW IT WORKS</a>
  <a style="left:740px">PRICING</a>
  <a style="left:847px">CONTACT</a>
  <span class="btn btn-blue" style="left:958px;top:22px;width:128px;height:42px;font-size:14.5px">FREE TRAIL</span>
</nav>

<section class="abs hero">
  <div class="abs hero-photo" role="img" aria-label="Photo of a team gathered around a laptop at a wooden table"></div>
  <svg class="abs" style="left:0;top:0" width="540" height="471" viewBox="0 0 540 471">
    <path d="M0 0H500C522 0 524 25 515 50L420 410C408 450 380 471 330 471H0Z" fill="#0054aa"/>
  </svg>
  <div class="abs hero-kicker">AUTOMATE YOUR BLOG</div>
  <h1 class="abs hero-h">POSTING WITH AI</h1>
  <p class="abs hero-p">Transform your blogging experience with our<br>AI-powered platform that not only generates and<br>optimizes content tailored</p>
  <span class="btn btn-white" style="left:44px;top:333px;width:205px;height:57px;font-size:21px">GET STARTED</span>
</section>

<section>
  <div class="bar" style="left:112px;top:703px"></div>
  <h2 class="title" style="left:112px;top:725px">OUR <span>PRICING</span></h2>
  <p class="copy" style="left:112px;top:791px">The purpose of this platform is to allow<br>anyone to start a blog and automate the<br>process &nbsp;of creating content and posting it<br>to the blog.</p>
  <p class="copy" style="left:112px;top:954px">The platform can be used to sell unique<br>accounts to multiple users. There<br>must be a subscription plan and a 14-day<br>free trial. The subscriptions are:</p>
  <span class="btn btn-blue" style="left:113px;top:1134px;width:178px;height:50px;font-size:18px">VIEW PLANS</span>
  <div class="abs price-bg"></div>
  <div class="card" style="left:495px">
    <svg width="84" height="92" viewBox="0 0 84 92" fill="none" stroke="#0054aa" stroke-width="3"><rect x="6" y="4" width="58" height="82" rx="6"/><rect x="18" y="0" width="34" height="10" rx="3" fill="#e8f1f8"/><circle cx="20" cy="30" r="4"/><circle cx="20" cy="48" r="4"/><circle cx="20" cy="66" r="4"/><path d="M30 30h24M30 48h20M30 66h14"/><path d="M52 78l22-24 8 7-22 24-10 3z" stroke="#0094d4"/></svg>
    <h3>BASE PLAN</h3><hr>
    <p>1 blog post (up to 2,000<br>words) every month</p>
    <span class="btn btn-blue">$9.99/MONTH</span>
  </div>
  <div class="card" style="left:802px">
    <svg width="84" height="92" viewBox="0 0 84 92" fill="none" stroke="#0054aa" stroke-width="3"><rect x="6" y="4" width="58" height="82" rx="6"/><rect x="18" y="0" width="34" height="10" rx="3" fill="#e8f1f8"/><circle cx="20" cy="30" r="4"/><circle cx="20" cy="48" r="4"/><circle cx="20" cy="66" r="4"/><path d="M30 30h24M30 48h20M30 66h14"/><path d="M52 78l22-24 8 7-22 24-10 3z" stroke="#0094d4"/></svg>
    <h3>PREMIUM PLAN</h3><hr>
    <p>1 blog post (up to 2,000<br>words) every week</p>
    <span class="btn btn-blue">$14.99/MONTH</span>
  </div>
</section>

<section class="abs about">
  <div class="abs about-shape"></div>
  <div class="abs dash" role="img" aria-label="Illustration of an analytics dashboard with charts and a calendar"></div>
  <div class="bar" style="left:680px;top:61px;background:#fff"></div>
  <h2 class="title" style="left:680px;top:83px;color:#fff;font-size:36px">ABOUT THE PLATFORM</h2>
  <p class="copy" style="left:680px;top:150px;color:#fff">The platform will require a list of blog topics. Based<br>on the topics list, the software will &nbsp;need to<br>automatically send prompts to TextMind in the<br>specified intervals (monthly, &nbsp;weekly, or daily),<br>receive the blog content, and post it to the blog.</p>
  <span class="btn btn-white" style="left:680px;top:377px;width:177px;height:50px;font-size:18px">LEARN MORE</span>
</section>

<section>
  <div class="bar" style="left:561px;top:1856px"></div>
  <h2 class="title" style="left:0;top:1878px;width:1200px;text-align:center">HOW TO SET UP THE <span>AUTO-BLOG</span></h2>
  <div class="step" style="left:110px">
    <svg width="54" height="48" viewBox="0 0 54 48" fill="none" stroke="#0054aa" stroke-width="2.5"><rect x="2" y="2" width="44" height="40" rx="3"/><path d="M2 12h44M10 22h20M10 30h14"/><path d="M36 40l14-14 3 3-14 14-5 1z" stroke="#0094d4"/></svg>
    <span>SELECT FREQUENCY OF<br>AUTOMATED BLOG POSTS<br>(DAILY, WEEKLY, OR<br>MONTHLY)</span>
  </div>
  <div class="step active" style="left:360px">
    <svg width="44" height="48" viewBox="0 0 44 48" fill="none" stroke="#fff" stroke-width="2.5"><rect x="8" y="2" width="34" height="38" rx="3"/><rect x="2" y="10" width="34" height="36" rx="3" fill="#0677ba"/><path d="M8 20h22M8 28h12M8 36h22"/></svg>
    <span>NAME YOUR BLOG</span>
  </div>
  <div class="step" style="left:609px">
    <svg width="50" height="48" viewBox="0 0 50 48" fill="none" stroke="#0054aa" stroke-width="2.5"><circle cx="22" cy="24" r="18"/><path d="M14 20h14M14 28h10"/><path d="M30 26l16-16 3 3-16 16-5 1z" stroke="#0094d4"/></svg>
    <span>SELECT YOUR BLOG<br>TOPICS (OR LET AI<br>CHOOSE THEM FOR YOU)</span>
  </div>
  <div class="step" style="left:858px">
    <svg width="50" height="48" viewBox="0 0 50 48" fill="none" stroke="#0054aa" stroke-width="2.5"><rect x="4" y="4" width="38" height="36" rx="3"/><path d="M4 14h38M12 24h22M12 32h14"/><path d="M34 42l12-12" stroke="#0094d4"/></svg>
    <span>GO DO SOMETHING ELSE<br>AND LET AI DO ALL YOUR<br>BLOGGING FOR YOU!</span>
  </div>
</section>

<section>
  <div class="bar" style="left:108px;top:2372px"></div>
  <h2 class="title" style="left:108px;top:2394px">OUR <span>BENEFITS</span></h2>
  <p class="copy" style="left:108px;top:2464px">Lorem ipsum dolor sit amet, consectetur adipiscing elit,<br>sed do eiusmod tempor incididunt ut labore et dolore<br>magna aliqua.</p>
  <ul class="abs ben-list">
    <li><svg width="22" height="22" viewBox="0 0 22 22" fill="none" stroke="#0094d4" stroke-width="2"><circle cx="11" cy="11" r="9"/><path d="M6 11l4 4 9-10"/></svg>Lorem ipsum dolor sit consectetur</li>
    <li><svg width="22" height="22" viewBox="0 0 22 22" fill="none" stroke="#0094d4" stroke-width="2"><circle cx="11" cy="11" r="9"/><path d="M6 11l4 4 9-10"/></svg>Lorem ipsum dolor sit consectetur</li>
    <li><svg width="22" height="22" viewBox="0 0 22 22" fill="none" stroke="#0094d4" stroke-width="2"><circle cx="11" cy="11" r="9"/><path d="M6 11l4 4 9-10"/></svg>Lorem ipsum dolor sit consectetur</li>
    <li><svg width="22" height="22" viewBox="0 0 22 22" fill="none" stroke="#0094d4" stroke-width="2"><circle cx="11" cy="11" r="9"/><path d="M6 11l4 4 9-10"/></svg>Lorem ipsum dolor sit consectetur</li>
    <li><svg width="22" height="22" viewBox="0 0 22 22" fill="none" stroke="#0094d4" stroke-width="2"><circle cx="11" cy="11" r="9"/><path d="M6 11l4 4 9-10"/></svg>Lorem ipsum dolor sit consectetur</li>
  </ul>
  <div class="abs ben-photo" role="img" aria-label="Photo of a person typing on a laptop at a desk with a vase of flowers"></div>
</section>

<footer class="abs footer">
  <svg class="abs foot-panel" viewBox="0 0 540 427" width="540" height="427">
    <path d="M0 0H500C530 0 540 20 530 50L430 390C420 415 400 427 370 427H0Z" fill="#e3ebf5"/>
  </svg>
  <h3 class="foot-h" style="left:89px;top:97px">CONTACT US</h3>
  <ul class="abs contact" style="left:89px;top:140px;list-style:none">
    <li><svg width="20" height="20" viewBox="0 0 20 20" fill="#0054aa"><path d="M4 1l4 4-2 3c1 2 3 4 5 5l3-2 4 4-2 3C9 18 2 11 1 3z"/></svg>+1 555 010 0199</li>
    <li><svg width="20" height="16" viewBox="0 0 20 16" fill="#0054aa"><path d="M0 0h20v16H0z"/><path d="M1 1l9 8 9-8" stroke="#e3ebf5" stroke-width="1.5" fill="none"/></svg>HELLO@POSTNOOK.IN</li>
    <li><svg width="16" height="22" viewBox="0 0 16 22" fill="#0054aa"><path d="M8 0a8 8 0 0 1 8 8c0 6-8 14-8 14S0 14 0 8a8 8 0 0 1 8-8zm0 5a3 3 0 1 0 0 6 3 3 0 0 0 0-6z"/></svg>BOX NO.412, POSTNOOK &nbsp;560 214</li>
  </ul>
  <div class="logo" style="left:89px;top:375px;font-size:30px"><i style="width:34px;height:34px"></i>POSTNOOK</div>
  <h3 class="foot-h" style="left:621px;top:140px">QUICK LINKS</h3>
  <ul class="links" style="left:621px;top:200px"><li>HOME</li><li>HOW IT WORKS</li><li>PRICING</li><li>PLATFORM</li><li>CONTACT</li></ul>
  <h3 class="foot-h" style="left:861px;top:140px">OTHER LINKS</h3>
  <ul class="links" style="left:861px;top:200px"><li>CAREERS</li><li>RESOURCES</li><li>SITE MAP</li><li>TERMS OF USE</li><li>PRIVACY POLICY</li></ul>
  <div class="abs rule"></div>
  <div class="abs copyright">@2024 COPYRIGHTS - ALL RIGHTS RESERVED</div>
  <div class="abs pays"><span>Orvexa</span><span>Brimlo</span><span>Tellupa</span><span>Quendry</span><span>Zarnipay</span></div>
</footer>

</body>
</html>
```